Dov's Personal Training -> also needs a logo

Services Frankston, Mornington, and Somerville

Specializes in in-home personal training

VaultPace style workouts

Not really preferential colors but needs to look modern and not stock photo

Industry/Entity Type

Training

Requirements
Must have
• 30% off first time customers on a package of 10

```html
<!DOCTYPE html>
<html lang="en">
<head>
<meta charset="utf-8">
<title>Dov's Personal Training – First Session Offer</title>
<link rel="stylesheet" href="https://fonts.googleapis.com/css2?family=Archivo+Black&family=Archivo:wght@800&family=Open+Sans:wght@400;600;800&display=swap">
<style>
  :root {
    --ink: #333638;
    --sky: #3ea2f2;
    --brand-blue: #3385f5;
    --brand-orange: #fb7f0d;
    --brand-aqua: #72f7e1;
    --rule-orange: #f6a04e;
    --bg-light: #ffffff;
    --bg-mid: #e9ebeb;
    --bg-dark: #b9bebe;
  }
  * { margin: 0; padding: 0; box-sizing: border-box; }
  html, body { width: 1200px; height: 900px; overflow: hidden; }
  body {
    background: var(--bg-mid);
    font-family: "Open Sans", Arial, sans-serif;
    color: var(--ink);
  }
  .flyer {
    position: relative;
    width: 1200px;
    height: 900px;
    overflow: hidden;
    background:
      radial-gradient(ellipse 70% 55% at 50% 40%, var(--bg-light) 0%, rgba(255,255,255,0) 100%),
      linear-gradient(180deg, #ececec 0%, #f7f7f7 25%, #e6e8e8 75%, var(--bg-dark) 100%);
  }
  .stripes { position: absolute; inset: 0; }
  .brand-name {
    position: absolute;
    left: 80px; top: 348px;
    font-weight: 600;
    color: var(--ink);
    line-height: 1;
  }
  .brand-name .word {
    display: block;
    font-size: 66px;
    letter-spacing: 0.38em;
  }
  .brand-name .tagline {
    display: block;
    margin-top: 16px;
    font-size: 28px;
    letter-spacing: 0;
  }
  .brand-rule {
    position: absolute;
    left: 80px; top: 494px;
    width: 296px; height: 7px;
    background: var(--rule-orange);
  }
  .info { position: absolute; left: 80px; line-height: 1; }
  .info-heading {
    font-weight: 800;
    font-size: 38px;
    letter-spacing: 0;
  }
  .areas { top: 532px; }
  .areas .info-heading { letter-spacing: 0.03em; }
  .areas li { list-style: none; }
  .areas .frankston { font-size: 35px; margin-top: 5px; }
  .areas .mornington { font-size: 30px; margin-top: 6px; }
  .areas .somerville { font-size: 34px; margin-top: 5px; }
  .specialties { top: 704px; }
  .specialties li { list-style: none; font-size: 40px; margin-top: 5px; letter-spacing: 0.01em; }
  .offer {
    position: absolute;
    left: 762px; top: 24px;
    color: var(--sky);
  }
  .offer-big {
    font-family: "Archivo Black", "Arial Black", sans-serif;
    font-size: 160px;
    line-height: 145px;
    letter-spacing: -0.01em;
  }
  .offer-terms {
    font-family: "Archivo", Arial, sans-serif;
    font-weight: 800;
    font-size: 40px;
    line-height: 42px;
    margin-top: 2px;
    letter-spacing: -0.005em;
  }
</style>
</head>
<body>
<main class="flyer">
  <svg class="stripes" width="1200" height="900" viewBox="0 0 1200 900" aria-hidden="true">
    <polygon points="700,900 1200,412 1200,900" fill="var(--brand-aqua)"/>
    <polygon points="836,900 1200,545 1200,900" fill="var(--brand-orange)"/>
    <polygon points="974,900 1200,682 1200,900" fill="var(--brand-blue)"/>
  </svg>

  <h1 class="brand-name">
    <span class="word">DOV'S</span>
    <span class="tagline">PERSONAL TRAINING</span>
  </h1>
  <div class="brand-rule" aria-hidden="true"></div>

  <section class="info areas">
    <h2 class="info-heading">SERVICES:</h2>
    <ul>
      <li class="frankston">FRANKSTON</li>
      <li class="mornington">MORNINGTON</li>
      <li class="somerville">SOMERVILLE</li>
    </ul>
  </section>

  <section class="info specialties">
    <h2 class="info-heading">SPECIALIZES IN:</h2>
    <ul>
      <li>IN-HOME PERSONAL TRAINING</li>
      <li>VAULTPACE STYLE WORKOUTS</li>
    </ul>
  </section>

  <section class="offer">
    <p class="offer-big">30%<br>OFF</p>
    <p class="offer-terms">first time customers<br>on a package of 10</p>
  </section>
</main>
</body>
</html>
```